Customer Value Leaflet

We need a bi-fold brochure designing, based on the attached PDF wireframes. Our company name is brambleharvik.com (of which the logo is currently being designed). The corporate colour is orange (the exact shade of which we are happy to leave to the designers discretion).

The leaflet will distributed to customer experience experts and marketers so the design needs to be bright, engaging, clean and simple. Design is critical.

It Company

```html
<!DOCTYPE html>
<html lang="en">
<head>
<meta charset="utf-8">
<title>BrambleHarvik – Customer Value</title>
<link rel="stylesheet" href="https://fonts.googleapis.com/css2?family=Open+Sans:wght@300;400&display=swap">
<style>
  :root {
    --brand-orange: #fbad3c;
    --ink: #262626;
    --frame-width: 4px;
  }
  * { margin: 0; padding: 0; box-sizing: border-box; }
  html, body {
    width: 1200px;
    height: 1200px;
    overflow: hidden;
    background: var(--brand-orange);
  }
  .panel {
    position: relative;
    width: 1200px;
    height: 1200px;
    background: var(--brand-orange);
    font-family: "Open Sans", sans-serif;
    color: var(--ink);
  }
  .panel__texture {
    position: absolute;
    inset: 0;
    background: var(--brand-orange);
  }
  .panel__frame {
    position: absolute;
    inset: 0;
  }
  .brand-name {
    position: absolute;
    left: 50px;
    top: 34px;
    font-size: 23px;
    font-weight: 400;
    line-height: 32px;
    letter-spacing: 0.2px;
  }
  .headline {
    position: absolute;
    left: 0;
    width: 1200px;
    text-align: center;
    font-weight: 300;
  }
  .headline__lead {
    top: 372px;
    font-size: 54px;
    line-height: 70px;
  }
  .headline__main {
    font-size: 128px;
    line-height: 140px;
    letter-spacing: -1px;
  }
  .headline__main--first { top: 450px; }
  .headline__main--second { top: 590px; }
  .headline__tail {
    top: 725px;
    font-size: 54px;
    line-height: 70px;
  }
</style>
</head>
<body>
  <main class="panel">
    <div class="panel__texture" role="img" aria-label="Faint dot grid pattern over the orange background"></div>

    <svg class="panel__frame" width="1200" height="1200" viewBox="0 0 1200 1200" aria-hidden="true">
      <g fill="none" stroke="var(--ink)" stroke-width="4">
        <polyline points="222,50 1150,50 1150,1150 52,1150 52,72"/>
        <line x1="297" y1="410" x2="480" y2="410" stroke-width="3"/>
        <line x1="730" y1="410" x2="905" y2="410" stroke-width="3"/>
        <line x1="408" y1="762" x2="463" y2="762" stroke-width="3"/>
        <line x1="740" y1="762" x2="793" y2="762" stroke-width="3"/>
      </g>
    </svg>

    <p class="brand-name">BrambleHarvik</p>

    <p class="headline headline__lead">We’re a</p>
    <h1 class="headline headline__main headline__main--first">CUSTOMER</h1>
    <h1 class="headline headline__main headline__main--second">VALUE</h1>
    <p class="headline headline__tail">company</p>
  </main>
</body>
</html>
```